Velmarotix - world unique technology for better life - please let them know who am i at first sight

We need a new business card for company which is a provider of unique crystal based technology suitable for all living being. For more information and final design you can use our brochure (our colours are black and blue from brochure).
We use Verdana font

Industry/Entity Type

Business

Contact Information for Business Card

regular dimension

Font styles to use
Other font styles liked:
• Verdana

Requirements
Must have
• Logo
• name
• function/position
• phone
• mobile
• e-mail
• adress
Nice to have
• inovative design (technology directed)

```html
<!DOCTYPE html>
<html lang="en">
<head>
<meta charset="utf-8">
<title>Velmarotix – Business Card</title>
<link rel="stylesheet" href="https://fonts.googleapis.com/css2?family=Open+Sans:wght@300;400;700&display=swap">
<style>
  :root {
    --backdrop: #cfcb9a;
    --card-black: #050505;
    --brand-blue: #1e9ad6;
    --wordmark-blue: #2aa3dd;
    --emblem-blue: #3f7896;
    --emblem-deep: #2c5a72;
    --text-light: #e6e6e6;
    --text-white: #ffffff;
  }
  * { margin: 0; padding: 0; box-sizing: border-box; }
  html, body {
    width: 1200px;
    height: 394px;
    overflow: hidden;
    background: var(--backdrop);
    font-family: "Open Sans", Verdana, sans-serif;
  }
  .canvas {
    position: relative;
    width: 1200px;
    height: 394px;
  }
  .card {
    position: absolute;
    top: 36px;
    width: 553px;
    height: 317px;
    background: var(--card-black);
    overflow: hidden;
  }
  .card--front { left: 28px; }
  .card--back { left: 618px; }

  .emblem-area {
    position: absolute;
    top: -20px;
    width: 360px;
    height: 360px;
    border-radius: 50%;
    background: radial-gradient(circle, var(--emblem-deep) 0%, var(--emblem-blue) 70%);
  }
  .card--front .emblem-area { left: 391px; }
  .card--back .emblem-area { left: -199px; }

  .holder-name {
    position: absolute;
    left: 23px;
    top: 40px;
    font-size: 27px;
    font-weight: 700;
    letter-spacing: 1.5px;
    color: var(--brand-blue);
    text-transform: uppercase;
    white-space: nowrap;
  }
  .holder-role {
    position: absolute;
    left: 23px;
    top: 76px;
    font-size: 22px;
    font-weight: 400;
    color: var(--text-light);
    text-transform: uppercase;
    white-space: nowrap;
  }
  .contact-list {
    position: absolute;
    left: 23px;
    top: 130px;
    list-style: none;
  }
  .contact-list li {
    display: flex;
    align-items: center;
    height: 29px;
    font-size: 16px;
    color: var(--text-white);
    white-space: nowrap;
  }
  .contact-icon {
    width: 15px;
    height: 15px;
    margin-right: 7px;
    fill: var(--brand-blue);
    flex: none;
  }
  .address {
    position: absolute;
    left: 23px;
    top: 273px;
    font-size: 15.5px;
    color: var(--text-white);
    white-space: nowrap;
  }

  .wordmark {
    position: absolute;
    left: 197px;
    top: 117px;
    font-size: 52px;
    font-weight: 300;
    letter-spacing: 3px;
    color: var(--wordmark-blue);
    line-height: 1;
    white-space: nowrap;
  }
</style>
</head>
<body>
<main class="canvas">

  <section class="card card--front" aria-label="Business card front">
    <div class="emblem-area" role="img" aria-label="Brand emblem area (right half of the ring symbol)"></div>

    <h1 class="holder-name">Mirela Kovandic</h1>
    <p class="holder-role">Founder and CEO</p>

    <ul class="contact-list">
      <li>
        <svg class="contact-icon" viewBox="0 0 16 16" aria-hidden="true">
          <circle cx="8" cy="8" r="7.3" fill="none" stroke="var(--brand-blue)" stroke-width="1.2"/>
          <path d="M5.2 4.2l1.4-.4 1 2-1 .8c.4 1 1.1 1.8 2 2.3l.9-.9 2 1-.4 1.4c-2.9.2-6-2.9-5.9-6.2z"/>
        </svg>
        012-345-6789
      </li>
      <li>
        <svg class="contact-icon" viewBox="0 0 16 16" aria-hidden="true">
          <rect x="4" y="1" width="8" height="14" rx="1.3"/>
          <rect x="5.3" y="3" width="5.4" height="5" fill="var(--card-black)"/>
          <rect x="5.3" y="9.5" width="5.4" height="4" fill="var(--card-black)"/>
        </svg>
        012-345-6789
      </li>
      <li>
        <svg class="contact-icon" viewBox="0 0 16 16" aria-hidden="true">
          <path d="M1 6l7-4.5L15 6v8H1z"/>
          <path d="M1.6 6.4L8 10.4l6.4-4" fill="none" stroke="var(--card-black)" stroke-width="1.2"/>
        </svg>
        info@velmarotix.com
      </li>
      <li>
        <svg class="contact-icon" viewBox="0 0 16 16" aria-hidden="true">
          <g fill="none" stroke="var(--brand-blue)" stroke-width="1.3">
            <circle cx="8" cy="8" r="6.6"/>
            <ellipse cx="8" cy="8" rx="3" ry="6.6"/>
            <path d="M1.5 8h13M2.6 4.6h10.8M2.6 11.4h10.8"/>
          </g>
        </svg>
        www.velmarotix.cu
      </li>
    </ul>

    <p class="address">Street Name, City Name, Zipcode-01234</p>
  </section>

  <section class="card card--back" aria-label="Business card back">
    <div class="emblem-area" role="img" aria-label="Brand emblem area (left half of the ring symbol)"></div>
    <p class="wordmark">VELMAROTIX</p>
  </section>

</main>
</body>
</html>
```